Larvik GmbH needs a sensational homepage!

A draft of the performances and the logo were uploaded in the attachment. The homepage should be adapted to the colors of the logo. Either pictures, graphics or icons of the respective topic are to be used for the buttons. Social media Linkedin, Youtube, Instagram should not be missing. An imprint, contact form with telephone number and email address should be given on the home page. The page should definitely be designed to be responsive for all end devices. Texts as well as images and videos are inserted in the sub-menus or pages. Only the structure and a simple application should be given. We have already secured the domain www.larvik-demo.at.
We are a young, dynamic company with a high technical affinity. Ask for creative suggestions. If something is needed, please contact us.

Target Market(s)

Construction industry, client

Requirements
Must have
• see description
Should not have
• shouldn't be colorful and playful

```html
<!DOCTYPE html>
<html lang="en">
<head>
<meta charset="utf-8">
<title>Larvik GmbH</title>
<link href="https://fonts.googleapis.com/css2?family=Marcellus&family=Roboto:wght@400;500;700&display=swap" rel="stylesheet">
<style>
:root{
  --ink:#2b2f35;
  --dark:#3c4148;
  --muted:#6b6f75;
  --line:#d9dadc;
  --soft:#f1f1f2;
  --white:#ffffff;
  --overlay:rgba(150,152,156,.88);
  --night:#1d2127;
}
*{box-sizing:border-box;margin:0;padding:0}
html,body{width:1200px;height:3684px;overflow:hidden}
body{font-family:"Roboto",sans-serif;color:var(--ink);background:var(--white);position:relative}
a{color:inherit;text-decoration:none}

.site-header{position:absolute;left:0;top:0;width:1200px;height:132px}
.brand{position:absolute;left:88px;top:18px;display:flex;align-items:center;gap:14px;font-family:"Marcellus",serif;font-size:46px;letter-spacing:6px;color:var(--dark)}
.brand .mark{width:14px;height:14px;background:var(--dark)}
.call-btn{position:absolute;right:88px;top:24px;height:40px;padding:0 18px;background:var(--dark);color:var(--white);font-size:15px;font-weight:500;line-height:40px;border-radius:3px}
.main-nav{position:absolute;left:88px;top:92px;width:1024px;display:flex;justify-content:space-between;font-size:15px;text-transform:uppercase;color:var(--muted)}
.main-nav a{padding:4px 8px}
.main-nav a.active{color:var(--ink);border-bottom:2px solid var(--ink)}

.hero{position:absolute;left:88px;top:132px;width:1024px;height:616px;background:linear-gradient(180deg,#5f9bd6 0%,#9cc7ec 45%,#8fae7a 72%,#4f7a33 100%)}
.hero-box{position:absolute;left:464px;top:176px;width:536px;height:232px;background:var(--overlay);padding:34px 34px}
.hero-box h1{font-family:"Marcellus",serif;font-weight:400;font-size:46px;letter-spacing:3px;color:var(--white)}
.hero-box p{margin-top:12px;font-size:19px;line-height:26px;color:var(--white)}
.btn{display:inline-block;background:var(--dark);color:var(--white);font-size:15px;font-weight:500;text-transform:uppercase;letter-spacing:1px;padding:0 26px;height:44px;line-height:44px}
.hero-box .btn{margin-top:18px}

.about{position:absolute;left:88px;top:848px;width:1024px;height:452px}
.about-photo{position:absolute;left:0;top:0;width:504px;height:440px;background:linear-gradient(135deg,#9aa3ab,#d4c39b 45%,#6f7b86);box-shadow:10px 10px 0 var(--line)}
.about-text{position:absolute;left:532px;top:20px;width:492px}
.about-text h2{font-family:"Marcellus",serif;font-weight:400;font-size:54px;letter-spacing:4px}
.about-text p{margin-top:18px;font-size:15px;line-height:26px;color:var(--muted)}
.about-text .btn{margin-top:28px}

.section-title{position:absolute;left:0;width:1200px;text-align:center;font-family:"Marcellus",serif;font-weight:400;font-size:54px;letter-spacing:4px;color:var(--ink)}
.section-sub{position:absolute;left:0;width:1200px;text-align:center;font-size:15px;color:var(--muted)}

.features{position:absolute;left:88px;top:1490px;width:1024px;display:flex;justify-content:space-between}
.feature{width:300px;text-align:center}
.feature svg{width:76px;height:76px}
.feature h3{margin-top:14px;font-size:21px;font-weight:500}
.feature p{margin-top:10px;font-size:15px;line-height:24px;color:var(--muted)}

.services{position:absolute;left:0;top:1860px;width:1200px;height:700px;background:var(--soft)}
.cards{position:absolute;left:88px;top:192px;width:1024px;display:flex;justify-content:space-between}
.card{position:relative;width:332px;height:372px;display:flex;align-items:center;justify-content:center;text-align:center;color:var(--white);font-size:26px;font-weight:500;line-height:32px}
.card.scaffold{background:linear-gradient(160deg,#bcc3c9,#7d8690 60%,#5c636b)}
.card.redev{background:linear-gradient(160deg,#3b6fb3,#9a8a79 55%,#4e555d)}
.card.screed{background:linear-gradient(180deg,#8fae6a 0%,#9aa0a6 30%,#7c8186 100%)}
.services .btn{position:absolute;left:492px;top:588px;width:216px;text-align:center;padding:0}

.reviews{position:absolute;left:88px;top:2790px;width:1024px;display:flex;justify-content:space-between}
.review{width:300px;text-align:center}
.review .quote{font-family:"Marcellus",serif;font-size:56px;line-height:40px;color:var(--dark)}
.review p{margin-top:10px;font-size:15px;line-height:24px;color:var(--muted)}
.review .name{margin-top:14px;font-size:15px;font-weight:500;color:var(--ink)}

.contact{position:absolute;left:0;top:3080px;width:1200px;height:540px;background:linear-gradient(100deg,#1b1f25 0%,#24272d 40%,#4a3a2e 70%,#6a4a33 85%,#2b2520 100%);color:var(--white)}
.contact-photo{position:absolute;right:0;top:0;width:700px;height:540px;background:radial-gradient(ellipse at 70% 20%,rgba(200,130,70,.35),rgba(20,20,24,0) 70%)}
.contact-info{position:absolute;left:88px;top:90px;width:470px}
.contact-info h2{font-size:46px;font-weight:500;letter-spacing:1px}
.contact-info p{margin-top:16px;font-size:15px;line-height:24px;color:#d6d7d9}
.contact-info address{margin-top:18px;font-style:normal;font-size:15px;line-height:26px;color:#d6d7d9}
.contact-brand{position:absolute;left:88px;top:420px;display:flex;align-items:center;gap:14px;font-family:"Marcellus",serif;font-size:44px;letter-spacing:6px;color:var(--white)}
.contact-brand .mark{width:14px;height:14px;background:var(--white)}
.form{position:absolute;left:612px;top:110px;width:500px}
.field{height:72px;border-bottom:1px solid rgba(255,255,255,.45);font-size:15px;color:#e6e6e8;padding-top:8px}
.form .submit{margin-top:24px;height:44px;width:500px;background:var(--dark);color:var(--white);text-align:center;line-height:44px;font-size:15px;font-weight:500;text-transform:uppercase;letter-spacing:1px}

.site-footer{position:absolute;left:0;top:3620px;width:1200px;height:64px;background:var(--white);font-size:13px;color:var(--muted)}
.site-footer .copy{position:absolute;left:88px;top:24px}
.socials{position:absolute;right:88px;top:20px;display:flex;gap:14px;align-items:center}
.socials i{display:block;width:20px;height:20px;border-radius:50%;background:var(--dark)}
.socials span{margin-left:10px}
</style>
</head>
<body>

<header class="site-header">
  <a class="brand" href="#"><span class="mark"></span>LARVIK</a>
  <a class="call-btn" href="#">CALL US : +43 555 210 340</a>
  <nav class="main-nav">
    <a class="active" href="#">Home</a>
    <a href="#">About us</a>
    <a href="#">Scaffolding ▾</a>
    <a href="#">Rehabilitation project management ▾</a>
    <a href="#">Screed &amp; insulation ▾</a>
  </nav>
</header>

<section class="hero" role="img" aria-label="Photo of a modern family house on a green lawn under a blue sky">
  <div class="hero-box">
    <h1>LARVIK GMBH</h1>
    <p>Lorem ipsum dolor sit amet, consectetur adipiscing elit, sed do eiusmod tempor incididunt</p>
    <a class="btn" href="#">Get started</a>
  </div>
</section>

<section class="about">
  <div class="about-photo" role="img" aria-label="Photo of two construction professionals reviewing plans on a tablet"></div>
  <div class="about-text">
    <h2>ABOUT US</h2>
    <p>Lorem ipsum dolor sit amet, consectetur adipiscing elit, sed do eiusmod tempor incididunt ut labore et dolore magna aliqua. Ut enim ad minim veniam, quis nostrud exercitation ullamco laboris nisi ut aliquip ex ea commodo consequat. Duis aute irure dolor in reprehenderit in voluptate velit esse cillum dolore eu fugiat nulla pariatur. Excepteur sint occaecat cupidatat non proident, sunt in culpa qui officia deserunt mollit anim id est laborum.</p>
    <a class="btn" href="#">Learn more</a>
  </div>
</section>

<h2 class="section-title" style="top:1384px">WHAT WE DO</h2>
<div class="features">
  <div class="feature">
    <svg viewBox="0 0 76 76" fill="none" stroke="#2b2f35" stroke-width="3" stroke-linejoin="round"><path d="M10 44l20-20 12 4 18-10"/><path d="M10 44l16 16 30-22-8-14"/><path d="M30 50l8 6M36 44l8 6"/></svg>
    <h3>Easy Financing</h3>
    <p>Lorem ipsum dolor sit amet, consectetur adipiscing elit, sed do eiusmod tempor incididunt ut labore et dolore magna aliqua.</p>
  </div>
  <div class="feature">
    <svg viewBox="0 0 76 76" fill="none" stroke="#2b2f35" stroke-width="3" stroke-linejoin="round"><path d="M8 36L38 10l30 26"/><path d="M16 30v36h44V30"/><rect x="24" y="38" width="10" height="10"/><rect x="42" y="38" width="10" height="10"/><rect x="33" y="52" width="10" height="14"/></svg>
    <h3>High quality homes</h3>
    <p>Lorem ipsum dolor sit amet, consectetur adipiscing elit, sed do eiusmod tempor incididunt ut labore et dolore magna aliqua.</p>
  </div>
  <div class="feature">
    <svg viewBox="0 0 76 76" fill="none" stroke="#2b2f35" stroke-width="3" stroke-linejoin="round"><path d="M38 8l24 10v16c0 16-10 28-24 34C24 62 14 50 14 34V18z"/><path d="M27 37l8 8 15-16"/></svg>
    <h3>Licensed &amp; Insured</h3>
    <p>Lorem ipsum dolor sit amet, consectetur adipiscing elit, sed do eiusmod tempor incididunt ut labore et dolore magna aliqua.</p>
  </div>
</div>

<section class="services">
  <h2 class="section-title" style="top:84px">SERVICES</h2>
  <p class="section-sub" style="top:148px">Lorem ipsum dolor sit amet, consectetur adipiscing elit</p>
  <div class="cards">
    <a class="card scaffold" href="#" role="img" aria-label="Photo of a worker assembling scaffolding"><span>Scaffolding</span></a>
    <a class="card redev" href="#" role="img" aria-label="Photo of a modern residential building facade"><span>Redevelopment<br>Project management</span></a>
    <a class="card screed" href="#" role="img" aria-label="Photo of freshly poured screed floor"><span>Screed &amp; insulation</span></a>
  </div>
  <a class="btn" href="#">See all services</a>
</section>

<h2 class="section-title" style="top:2676px">SATISFIED CUSTOMERS</h2>
<div class="reviews">
  <div class="review"><div class="quote">❝</div><p>Lorem ipsum dolor sit amet, consectetur adipiscing elit, sed do eiusmod tempor incididunt ut labore et dolore magna aliqua.</p><div class="name">Mara Holm</div></div>
  <div class="review"><div class="quote">❝</div><p>Lorem ipsum dolor sit amet, consectetur adipiscing elit, sed do eiusmod tempor incididunt ut labore et dolore magna aliqua.</p><div class="name">Mara Holm</div></div>
  <div class="review"><div class="quote">❝</div><p>Lorem ipsum dolor sit amet, consectetur adipiscing elit, sed do eiusmod tempor incididunt ut labore et dolore magna aliqua.</p><div class="name">Mara Holm</div></div>
</div>

<section class="contact">
  <div class="contact-photo" role="img" aria-label="Photo of construction workers silhouetted against a sunset at a building site"></div>
  <div class="contact-info">
    <h2>GET IN TOUCH</h2>
    <p>Lorem ipsum dolor sit amet, consectetur adipiscing elit, sed do eiusmod tempor incididunt ut labore et dolore magna aliqua.</p>
    <address>Hafengasse 12, 4020 Linz<br>Austria<br>info@larvik-demo.at<br>+43 555 210 340</address>
  </div>
  <div class="contact-brand"><span class="mark"></span>LARVIK</div>
  <form class="form">
    <div class="field">Name</div>
    <div class="field">Email</div>
    <div class="field">Phone No.</div>
    <div class="field">Message</div>
    <div class="submit">Submit</div>
  </form>
</section>

<footer class="site-footer">
  <div class="copy">Copyright © 2021 Larvik GmbH All rights reserved. | Imprint</div>
  <div class="socials" aria-label="Social media links">
    <i title="Social profile 1"></i><i title="Social profile 2"></i><i title="Social profile 3"></i><span>ENG</span>
  </div>
</footer>

</body>
</html>
```